Visitenkarte für Ergotherapiepraxis
Zielgruppe
Wir arbeiten mit Kindern und Erwachsene jeden Alters.
Diese Personen kommen mit Beeinträchtigungen (körperlich, seelisch, schulisch) im täglichen Leben zu uns. Wir unterstützen unsere Patienten die Beeinträchtigungen zu verringern oder zu kompensieren und so den Alltag besser bewältigen zu können.
Aufgabenstellung
Ein Design was Kinder und Erwachsene anspricht, aber nicht zu verspielt wirkt. Es soll vertrauenserweckend sein. Eventuell sollte die Visitenkarte ein "aufgehendes oder erblühendes oder aufsteigendes" Element enthalten (=zu Beginn war die Beeinträchtigung dann steigt die Lebensqualität als Folge der Behandlung)
Daten vorn:
Ergotherapiepraxis

```html
<!DOCTYPE html>
<html lang="de">
<head>
<meta charset="utf-8">
<title>Visitenkarte Ergotherapiepraxis</title>
<link href="https://fonts.googleapis.com/css2?family=Barlow:wght@300;500;600&display=swap" rel="stylesheet">
<style>
  :root {
    --red: #990000;
    --green: #0f8f3e;
    --green-light: #1fa050;
    --grey-text: #5a5a5a;
    --faint: #ececec;
    --white: #ffffff;
    --frame: #1a1a1a;
    --frame-light: #b5b5b5;
  }
  * { margin: 0; padding: 0; box-sizing: border-box; }
  html, body { width: 773px; height: 1200px; overflow: hidden; background: var(--white); }
  body { position: relative; font-family: "Barlow", sans-serif; }

  .card { position: absolute; left: 183px; width: 392px; height: 254px; background: var(--white); overflow: hidden; }
  .card--front { top: 110px; border: 1px solid var(--frame); }
  .card--back { top: 381px; border: 1px solid var(--frame-light); }

  .band { position: absolute; left: 0; right: 0; background: var(--red); }
  .card--front .band--main { top: 160px; height: 57px; }
  .card--front .band--foot { top: 241px; height: 13px; }
  .card--back .band--main { top: 170px; height: 44px; }

  .brand { position: absolute; display: flex; align-items: center; gap: 8px; font-weight: 600; font-size: 26px; }
  .brand__dot { width: 18px; height: 18px; border-radius: 50%; background: currentColor; }
  .card--front .brand { left: 18px; top: 60px; color: var(--red); }
  .card--back .brand { left: 18px; top: 60px; color: var(--faint); font-size: 40px; }
  .card--back .brand__dot { width: 28px; height: 28px; }

  .title { position: absolute; left: 164px; top: 130px; font-size: 23px; line-height: 1; white-space: nowrap; }
  .title__main { color: var(--grey-text); font-weight: 500; }
  .title__sep { display: inline-block; width: 1px; height: 28px; background: var(--red); vertical-align: -6px; margin: 0 3px; }
  .title__sub { color: var(--green-light); font-weight: 300; }

  .name { position: absolute; left: 164px; top: 161px; color: var(--white); font-size: 20px; font-weight: 500; letter-spacing: 0.3px; }
  .phone { position: absolute; left: 163px; top: 196px; color: var(--white); font-size: 19px; font-weight: 500; }
  .address { position: absolute; left: 0; right: 0; top: 220px; text-align: center; padding-left: 8px; color: var(--green); font-size: 17.5px; font-weight: 500; white-space: nowrap; }

  .therapist { position: absolute; left: 166px; top: 136px; font-size: 15.5px; white-space: nowrap; line-height: 1; }
  .therapist__label { color: var(--green); font-weight: 600; letter-spacing: 0.4px; }
  .therapist__sep { display: inline-block; width: 1px; height: 30px; background: var(--red); vertical-align: -6px; margin: 0 3px 0 4px; }
  .therapist__value { color: var(--green-light); font-weight: 300; letter-spacing: 0.4px; }
</style>
</head>
<body>
  <section class="card card--front" aria-label="Vorderseite">
    <div class="brand"><span class="brand__dot"></span>Praxis Roth</div>
    <div class="band band--main"></div>
    <div class="band band--foot"></div>
    <p class="title"><span class="title__main">Ergotherapie</span><span class="title__sep"></span><span class="title__sub">praxis</span></p>
    <p class="name">Wilma Roth</p>
    <p class="phone">Tel. 033750/48150</p>
    <p class="address">Am Mühlenweg 12 | 14950 Lindental, OT Wiesenau</p>
  </section>

  <section class="card card--back" aria-label="Rückseite">
    <div class="brand"><span class="brand__dot"></span>Praxis Roth</div>
    <p class="therapist"><span class="therapist__label">Behandelnder</span><span class="therapist__sep"></span><span class="therapist__value">Therapeut/in:</span></p>
    <div class="band band--main"></div>
  </section>
</body>
</html>
```